I have a logo and need to design the business card and stationery.
Updates

The uploaded logo image named as GREYMARSH CONTRACTS which is to be replaced to GREYMARSH CONTRACTS. Kindly add below details and submit the designs- Company name- Greymarsh Engineering Contracts LLP Name & Post- Kelvan Joshi (Designated Partner) Address- Block No.317, Wing C, Tulvo Trade Court, Manek Pural Road, Ruparel Industrial Estate, Goregaon(E), Mumbai - 400 063 Contact- +91 97415 60382 Email- kelvanjoshi@mailbrook.example Website- www.greymarshcontracts.example Contact for Letterhead- +91-22-28754193

Hi Tovin Rahul, We are liking your Design #28860835. We have suggested some changes which are mentioned in feedback. Kindly revert with it asap to finalize this design.

Colors

Designer to choose colors to be used in the design.

```html
<!DOCTYPE html>
<html lang="en">
<head>
<meta charset="utf-8">
<title>Greymarsh Contracts – Business Card</title>
<link rel="stylesheet" href="https://fonts.googleapis.com/css2?family=Exo+2:wght@400;500;700;800&display=swap">
<style>
  :root {
    --stage: #d6d6d6;
    --card-light: #ffffff;
    --card-dark: #2f2f2f;
    --ink: #1f1f1f;
    --ink-soft: #4a4a4a;
    --rule: #9a9a9a;
    --band: #262626;
    --band-edge: #8c8c8c;
    --paper-text: #ffffff;
  }
  * { box-sizing: border-box; margin: 0; padding: 0; }
  html, body { width: 1200px; height: 866px; overflow: hidden; }
  body {
    background: var(--stage);
    font-family: "Exo 2", sans-serif;
    color: var(--ink);
    display: flex;
    flex-direction: column;
    align-items: center;
    justify-content: center;
    gap: 40px;
  }
  .card {
    position: relative;
    width: 560px;
    height: 320px;
    border-radius: 4px;
    overflow: hidden;
    box-shadow: 0 10px 24px rgba(0,0,0,0.25);
  }
  .card--front { background: var(--card-light); }
  .card--back  { background: var(--card-dark); }

  .brand {
    display: flex;
    align-items: center;
    gap: 12px;
    font-weight: 800;
    text-transform: uppercase;
    letter-spacing: 1px;
    line-height: 1.05;
  }
  .brand__mark { width: 38px; height: 38px; flex: none; }
  .card--front .brand { position: absolute; top: 40px; right: 40px; color: var(--ink); font-size: 22px; }
  .card--front .brand__mark { background: var(--ink); }
  .card--back .brand {
    position: absolute; inset: 0; justify-content: center;
    color: var(--paper-text); font-size: 34px; gap: 18px;
  }
  .card--back .brand__mark { width: 56px; height: 56px; background: var(--paper-text); }

  .person { position: absolute; top: 110px; left: 40px; width: 235px; }
  .person__name { font-size: 21px; font-weight: 800; letter-spacing: 1.5px; text-transform: uppercase; }
  .person__role { font-size: 14px; font-weight: 500; color: var(--ink-soft); margin-top: 2px; }
  .person__rule { border: 0; border-top: 1px solid var(--rule); margin: 10px 0; }
  .contact { list-style: none; font-size: 13.5px; font-weight: 500; }
  .contact li { display: flex; align-items: center; gap: 8px; margin-bottom: 4px; white-space: nowrap; }
  .contact svg { width: 12px; height: 12px; flex: none; }

  .address {
    position: absolute; right: 40px; top: 158px; width: 235px;
    font-size: 12px; font-weight: 500; text-align: right; line-height: 1.4;
    padding-bottom: 8px; border-bottom: 1px solid var(--rule);
  }
  .footer-band { position: absolute; left: 0; bottom: 0; width: 100%; height: 52px; }
  .website {
    position: absolute; right: 40px; bottom: 12px;
    color: var(--paper-text); font-size: 14px; font-weight: 700; letter-spacing: 1px;
  }
</style>
</head>
<body>

  <article class="card card--front" aria-label="Business card front">
    <div class="brand">
      <span class="brand__mark"></span>
      <span>Greymarsh<br>Contracts</span>
    </div>

    <section class="person">
      <h1 class="person__name">Kelvan Joshi</h1>
      <p class="person__role">Designated Partner</p>
      <hr class="person__rule">
      <ul class="contact">
        <li>
          <svg viewBox="0 0 24 24" aria-hidden="true"><path fill="currentColor" d="M6.6 10.8a15 15 0 0 0 6.6 6.6l2.2-2.2a1 1 0 0 1 1-.25 11.4 11.4 0 0 0 3.6.57 1 1 0 0 1 1 1V20a1 1 0 0 1-1 1A17 17 0 0 1 3 4a1 1 0 0 1 1-1h3.5a1 1 0 0 1 1 1c0 1.25.2 2.450.57 3.57a1 1 0 0 1-.25 1z"/></svg>
          +91 97415 60382
        </li>
        <li>
          <svg viewBox="0 0 24 24" aria-hidden="true"><path fill="currentColor" d="M2 5h20v14H2zm2 2v.5l8 5 8-5V7z"/></svg>
          kelvanjoshi@mailbrook.example
        </li>
      </ul>
    </section>

    <p class="address">Block No.317, Wing C, Tulvo Trade Court,<br>Manek Pural Road, Ruparel Industrial Estate,<br>Goregaon(E), Mumbai - 400 063</p>

    <svg class="footer-band" viewBox="0 0 560 52" preserveAspectRatio="none" aria-hidden="true">
      <path d="M0 22 H175 C195 22 195 6 215 6 H560 V8 H215 C197 8 197 24 175 24 H0 Z" fill="var(--band-edge)"/>
      <path d="M0 30 H175 C200 30 200 14 222 14 H560 V52 H0 Z" fill="var(--band)"/>
    </svg>
    <p class="website">www.greymarshcontracts.example</p>
  </article>

  <article class="card card--back" aria-label="Business card back">
    <div class="brand">
      <span class="brand__mark"></span>
      <span>Greymarsh<br>Contracts</span>
    </div>
  </article>

</body>
</html>
```